Silver Kite Venture Series Travel Brochure

I'm looking for a brochure design for a new travel product - Silver Kite Venture Series, catering for students above 12 years old. Target audience are schools that do destination projects. Brochure to be read by head teacher, parents and students.

Brochure should be A4 in size, 4-6 pages. Format of brochure is hard cover (a folder) with inlet for flyers. Flyers for destinations will be updated from time to time.

Finished job needs to be converted to electronic format for website and email proposal usage.

Attached is text to be used on brochure. Order of section can be adjusted.

For "Elements of the trip", please understand the contents and explain/display it in a graphic form.

For flyer, please come out with a template that I can use for other destinations. The main elements - what's included, number of days, location for pictures, itinerary, educational focus, should be alterable. Attached are text for two sample destinations.
Also attached (tour itinerary example) a version of flyer that I like.

I'm attaching some pictures here. If you find more suitable pictures, please feel free to use them.

Reason: I'm extending the deadline of this project by 4 days, as I need to add details & photo of another travel specialist in personnel session (total of 3 members). Also, in view of the amount of work a designer has to do for this project, I'm giving you more time for submission. Please do not hesitate to be in touch should you need more than 4 days extension. Thank you.

Target Market(s)

Schools - especially the head teacher and parents, to send students above 12 years old to travel

Industry/Entity Type

Electronic

Requirements
Must have
• This is a travel brochure with education elements in it. Parents feel better when their children are travelling for a purpose and lead by responsible teachers/adults whom they can trust. So, the design has to emphasis that education elements and safety are our utmost priority.
Nice to have
• We specialise in environmental study. So, it is nice to have the environmental touch in the design.
Should not have
• Our target market segment is the Middle East, which can be quite sensitive to religion. I prefer not to have any religious related illustration on the design.

```html
<!DOCTYPE html>
<html lang="en">
<head>
<meta charset="utf-8">
<title>Silver Kite Venture Series – Egypt Itinerary</title>
<link rel="stylesheet" href="https://fonts.googleapis.com/css2?family=Alfa+Slab+One&family=PT+Sans:ital,wght@0,400;0,700;1,700&display=swap">
<style>
  :root{
    --band-green:#9cc83b;
    --stem-green:#4f9a22;
    --sky-blue:#5ea3d9;
    --ink:#1d1d1b;
    --meal-blue:#1e4f93;
    --caption-band:rgba(18,40,70,.85);
    --page:#ffffff;
  }
  *{margin:0;padding:0;box-sizing:border-box}
  html,body{width:864px;height:1200px;overflow:hidden;background:var(--page)}
  body{position:relative;font-family:"PT Sans",Arial,sans-serif;color:var(--ink)}

  .day{position:absolute;left:66px;width:732px}
  .day--one{top:136px;height:318px;background:var(--band-green)}
  .day--two{top:468px;height:193px;background:var(--sky-blue)}
  .day--three{top:677px;height:333px;background:var(--band-green)}

  .photo{position:absolute;top:0;height:100%}
  .day--one .photo{left:0;width:247px;background:linear-gradient(180deg,#9db7c9 0%,#c9ab7e 45%,#a77c4c 100%)}
  .day--two .photo{right:0;width:246px;background:linear-gradient(160deg,#3b2a1c 0%,#8a5a2c 45%,#2b2f3a 100%)}
  .day--three .photo{left:0;width:242px;background:linear-gradient(180deg,#6aa5dc 0%,#a9c9e6 42%,#b9a27a 52%,#2f5f86 68%,#1c3e63 100%)}

  .caption{position:absolute;left:0;right:0;bottom:0;padding:11px 14px 12px;background:var(--caption-band);
    font-family:"Alfa Slab One",Georgia,serif;color:#fff;font-size:17.5px;line-height:1.15}
  .day--two .caption{text-align:center;padding:12px 10px 10px}

  .stem{position:absolute;width:5px;background:var(--stem-green)}

  .day-tab{position:absolute;height:40px;width:132px;border-radius:20px;background:var(--band-green);
    border:3px solid #fff;box-shadow:0 0 0 2px var(--stem-green);
    font-family:"Alfa Slab One",Georgia,serif;color:#fff;font-size:22px;line-height:34px;text-align:center;letter-spacing:.5px}

  .meals{position:absolute;top:10px;display:flex;align-items:center;gap:9px;
    font-family:"Alfa Slab One",Georgia,serif;color:var(--meal-blue);font-size:17px;line-height:1}
  .meals svg{width:16px;height:20px}

  .copy{position:absolute;font-size:10.5px;line-height:1.28;column-count:2;column-gap:18px;text-align:justify}
  .copy p{margin-bottom:5px}
  .copy h3{font-style:italic;font-weight:700;font-size:13.5px;margin:5px 0 0;text-align:left}
  .day--one .copy{left:269px;top:37px;width:446px}
  .day--two .copy{left:20px;top:69px;width:446px}
  .day--three .copy{left:269px;top:36px;width:446px}

  .contact{position:absolute;left:66px;top:1064px;font-size:10.4px;line-height:1.3}
</style>
</head>
<body>

<svg width="0" height="0" style="position:absolute" aria-hidden="true">
  <symbol id="icon-cutlery" viewBox="0 0 16 20">
    <g fill="none" stroke="currentColor" stroke-width="1.8" stroke-linecap="round">
      <path d="M2 1v5a2 2 0 0 0 4 0V1M4 1v18"/>
      <path d="M12 19V1c-2 1.5-3 4-3 7h3"/>
    </g>
  </symbol>
</svg>

<section class="day day--one">
  <div class="photo" role="img" aria-label="Photo of the Step Pyramid seen past a carved stone column in the desert">
    <div class="caption">Arrival at Cairo</div>
  </div>
  <div class="stem" style="left:245px;top:0;height:328px"></div>
  <div class="day-tab" style="left:240px;top:-20px">Day 1</div>
  <div class="meals" style="right:20px">
    <svg><use href="#icon-cutlery"/></svg>L/D
  </div>
  <div class="copy">
    <p><b>Ahlan!</b> Welcome to historical EGYPT!</p>
    <p>Upon arrival at Cairo Airport, you will be met and assisted through passport control.</p>
    <p>You will then travel to Giza to see the famous <b>Sphinx</b> and visit the <b>Great Pyramids.</b> Giza is the location of the Pyramid of Khufu (also known as the "Great Pyramid" and the "Pyramid of Cheops"); the somewhat smaller Pyramid of Khafre (or Kephren); and the relatively modest-sized Pyramid of Menkaure (or Mykerinus), along with a number of smaller satellite edifices known as "Queen's pyramids". <b>The Great Pyramid</b> was the centerpiece of an elaborate complex, which included several small pyramids, five boat pits, a mortuary temple, a causeway, a valley temple, and many flat-roofed tombs for officials and some members of the royal family. After this, you continue on to Sakkara with lunch at a restaurant en route.</p>
    <p>After lunch, visit the <b>Step Pyramid of Dzoser,</b> the oldest pyramid in Egypt. Built by the great architect Imhotep, the Step Pyramid shows the evolution from mastaba type tombs to the pyramid form. Nearby are tombs of kings and nobles dating from the earliest dynasties of the Old Kingdom period. From here you go to the ancient capital of <b>Memphis</b> to see the Alabaster Sphinx and the colossal statue of Rameses II.</p>
    <p>Overnight in Cairo.</p>
  </div>
</section>

<section class="day day--two">
  <div class="photo" role="img" aria-label="Photo of a lantern-lit evening bazaar street with shoppers">
    <div class="caption">Cairo Museum &amp;<br>Bazaar</div>
  </div>
  <div class="stem" style="left:484px;top:0;height:193px"></div>
  <div class="day-tab" style="left:360px;top:-17px">Day 2</div>
  <div class="meals" style="left:20px">B/D
    <svg><use href="#icon-cutlery"/></svg>
  </div>
  <div class="copy">
    <p>After breakfast, you will take a tour to the world famous <b>Egyptian Museum</b> with its 100,000 objects covering 4,000 years of ancient Egyptian civilization, including the treasures of Tutankhamen. You will then immerse into the old souq of Khan <b>El Khalili bazaar.</b></p>
    <p>In the evening, have a sumptuous dinner before transfer to railway station for departure to Aswan on first class sleeper train.</p>
  </div>
</section>

<section class="day day--three">
  <div class="photo" role="img" aria-label="Photo of Philae Temple on its island across the blue Nile water">
    <div class="caption">Aswan – Nile Cruise</div>
  </div>
  <div class="stem" style="left:245px;top:0;height:343px"></div>
  <div class="day-tab" style="left:240px;top:-20px">Day 3</div>
  <div class="meals" style="right:20px">
    <svg><use href="#icon-cutlery"/></svg>B/L/D
  </div>
  <div class="copy">
    <p>Upon arrival in Aswan, you will be transferred to the <b>Nile Cruise</b> terminal. Embark on your cruise, where you will be welcomed and briefed about your journey on the cruise.</p>
    <p>Sit back and relax for your tour of Aswan.</p>
    <h3>High dam</h3>
    <p>The high dam is the largest rock-filled dam in the world and one of the most important engineering feats of the 20th century, an artificial lake Nasser, with a surface of 4000 sq km lies behind the dam.</p>
    <h3>Unfinished obelisk</h3>
    <p>The unfinished obelisk is the largest known ancient obelisk, located in the northern region of the stone quarries of ancient Egypt in Aswan. It is unknown which pharaoh created this structure. It is nearly one third larger than any other ancient Egyptian obelisk. If finished it would have measured around 42 m (approximately 137 feet) and would have weighed nearly 1,200 tons.</p>
    <h3>Philae Temple</h3>
    <p>Philae Temple was dismantled and reassembled (on Agilika Island about 550 meters from its original home on Philae Island) High Dam was being constructed. The temple, dedicated to the goddess Isis, is in a beautiful setting which has been landscaped to match its original site. Its various shrines and sanctuaries, include The Vestibule of Nectanebos I, which is used as the entrance to the island.</p>
    <p>Overnight on Cruise.</p>
  </div>
</section>

<footer class="contact">
  <b>Silver Kite Venture Series</b><br>
  820 Palm Court Offices, Harbour Lake Towers,<br>
  PO Box 512760, Dubai, UAE<br>
  <b>Tel:</b> +971 4 555 0142<br>
  <b>Fax:</b> +971 4 555 0198<br>
  <b>Email:</b> info@silverkitetravel.com
</footer>

</body>
</html>
```